Pinecrest Harbor Foundation Web Design

The design we need is for a WordPress blog that will be our content platform. We are a registered 501(c)3 non-profit that focuses on financially supporting the treatment of cancer patients that have been told they have no hope and there is nothing the conventional medical system can do for them. Through this wesbite we want to both rasie awareness about the treatment options plus, raise funds for treating patients. The two primary target audiences of the site are...

1. Terminally ill patients and their families to let them know that there is an option other then hospice and that we are hear to support that option.

2. People looking to help donate to a worthwhile cause that resonates with them.

The website is https://pinecrestharborfoundation.org/

See attached logo designs!!!

Target Market(s)

Cancer patients and their families

Industry/Entity Type

Foundation

Font styles to use
Sans Serif

Colors
ffffff
fbed22

Requirements
Must have
• I like this look of this site. It is clean, simple, helpful, soft. I like the flow of the pages.
• http://www.meadowsforcalm.org/
• I like the design and flow but NOT the color or boldness
• https://tvbn-youth.org/
• I like this style for a donation page.
• https://www.tumorstudyhub.org/we-are-tsh/join-the-cause/donations/one-time-donation
• with the addition of a Would you like your employer to match? button.
Nice to have
• White black and gold - but soft
• Even possibly grayscale like the site I like.

```html
<!DOCTYPE html>
<html lang="en">
<head>
<meta charset="utf-8">
<title>Pinecrest Harbor Foundation</title>
<link rel="stylesheet" href="https://fonts.googleapis.com/css2?family=Roboto:wght@300;400;500;700&display=swap">
<style>
:root{
  --gold:#e6cd62;
  --gold-soft:#efdc8e;
  --gold-deep:#a8892a;
  --ink:#1b1b1b;
  --ink-soft:#2a2a2a;
  --white:#ffffff;
  --grey-card:#f2f2f0;
  --grey-text:#6c6c6c;
  --footer:#161616;
  --footer-text:#d9d9d9;
}
*{box-sizing:border-box;margin:0;padding:0}
html,body{width:1200px;height:2782px;overflow:hidden}
body{position:relative;font-family:'Roboto',sans-serif;color:var(--ink);background:var(--white)}
.abs{position:absolute}

/* hero */
.hero{left:0;top:0;width:1200px;height:658px;background:linear-gradient(90deg,#3e3e40 0%,#6f7073 45%,#4b4b4d 100%)}
.hero-portrait{left:560px;top:0;width:640px;height:658px;background:radial-gradient(ellipse at 55% 50%,#8b8486 0%,#726d70 35%,rgba(80,80,84,0) 70%)}
.menu-icon{left:1056px;top:16px;width:40px;height:26px}
.menu-icon span{display:block;height:4px;background:var(--white);margin-bottom:7px}
.ribbon-top{left:263px;top:0;width:149px;height:226px;background:var(--gold);display:flex;align-items:center;justify-content:center}
.ribbon-top .mark{width:62px;height:62px;border-radius:50%;background:var(--white)}
.ribbon-bottom{left:263px;top:390px;width:149px;height:195px}
.hero-title{left:100px;top:240px;width:460px;color:var(--white);text-align:center}
.hero-title .line1{font-size:41px;font-weight:500;letter-spacing:0.3px;line-height:50px}
.hero-title .line2{font-size:68px;font-weight:700;line-height:80px;margin-top:4px}
.hero-dots{left:122px;top:606px;display:flex;gap:8px}
.hero-dots i{width:9px;height:9px;border-radius:50%;background:var(--white)}
.hero-dots i.on{background:var(--gold);box-shadow:0 0 0 2px var(--white)}

/* intro & causes */
.causes-bg{left:0;top:658px;width:1200px;height:741px;background:linear-gradient(180deg,#ffffff 0%,#f2f1ef 40%,#e8e6e3 75%,#f4f3f2 100%)}
.intro{left:100px;top:702px;width:1000px;text-align:center;font-size:26.5px;line-height:34px;color:var(--ink)}
.divider{left:542px;top:828px;width:116px;height:4px;background:var(--ink)}
.section-title{font-weight:700;font-size:34px;text-align:center;letter-spacing:0.3px}
.causes-title{left:0;top:850px;width:1200px}
.causes-title em{font-style:normal;color:var(--gold-deep)}
.cause-card{top:940px;width:316px;height:422px;background:var(--gold);color:var(--ink)}
.cause-card .photo{width:316px;height:195px;background:linear-gradient(135deg,#cfcbc6,#8f8a84)}
.cause-card .progress{position:absolute;left:25px;top:178px;width:266px;height:34px;border-radius:17px;background:var(--white);box-shadow:0 2px 6px rgba(0,0,0,.2)}
.progress .track{position:absolute;left:16px;top:15px;width:205px;height:5px;background:#dcdcdc;border-radius:3px}
.progress .fill{width:50%;height:5px;background:var(--gold-deep);border-radius:3px}
.progress .pct{position:absolute;right:12px;top:9px;font-size:12px;font-weight:700;color:var(--ink)}
.cause-card .stats{position:absolute;left:30px;right:30px;top:240px;display:flex;justify-content:space-between;font-size:12.5px}
.cause-card .desc{position:absolute;left:30px;right:30px;top:282px;text-align:center;font-size:17px;line-height:21px}
.btn{display:inline-block;background:var(--ink-soft);color:var(--white);font-size:13px;font-weight:500;border-radius:20px;text-align:center}
.cause-card .btn{position:absolute;left:90px;top:362px;width:137px;height:34px;line-height:34px}

/* team */
.team-photo{left:0;top:1399px;width:700px;height:465px;background:linear-gradient(120deg,#b8b4a4 0%,#8a8a78 40%,#bdb3a8 70%,#8e97a2 100%)}
.team-panel{left:0;top:1399px;width:1200px;height:465px}
.team-title{left:681px;top:1480px;color:var(--ink);font-size:33px;font-weight:500;line-height:43px;letter-spacing:1.5px}
.team-text{left:681px;top:1592px;width:410px;color:var(--ink);font-size:14.5px;line-height:17.5px}
.team-btn{left:681px;top:1710px;width:152px;height:40px;line-height:40px;font-size:14px}

/* testimonials */
.testi-title{left:0;top:1916px;width:1200px}
.testi-card{top:2009px;width:438px;height:186px;background:var(--grey-card)}
.testi-card .avatar{position:absolute;left:22px;top:38px;width:94px;height:94px;border-radius:50%;background:linear-gradient(135deg,#b59d8a,#5e4e44)}
.testi-card .quote{position:absolute;left:140px;top:36px;width:270px;font-size:11px;line-height:17px;color:var(--grey-text)}
.testi-card .name{position:absolute;left:140px;top:134px;font-size:11px;font-weight:700;color:var(--gold-deep)}
.testi-dots{left:574px;top:2223px;display:flex;gap:6px}
.testi-dots i{width:12px;height:12px;border-radius:50%;background:#8c8c8c}

/* call bar */
.footer{left:0;top:2373px;width:1200px;height:409px;background:var(--footer)}
.callbar{left:102px;top:2278px;width:1000px;height:95px;background:var(--gold);color:var(--ink)}
.callbar .phone-icon{position:absolute;left:26px;top:28px;width:40px;height:40px}
.callbar .ask{position:absolute;left:90px;top:33px;font-size:13px;line-height:15px;letter-spacing:.5px}
.callbar .number{position:absolute;left:208px;top:24px;font-size:37px;font-weight:400;letter-spacing:1px}
.callbar .email{position:absolute;left:553px;top:30px;width:272px;height:35px;border-radius:18px;background:var(--white);font-size:13px;color:#9a9a9a;padding:10px 0 0 38px}
.callbar .email svg{position:absolute;left:14px;top:12px}
.callbar .subscribe{position:absolute;left:841px;top:30px;width:133px;height:35px;line-height:35px;font-size:13px;background:var(--ink-soft);color:var(--white);border-radius:18px;text-align:center}

/* footer */
.f-col{top:2410px;color:var(--footer-text)}
.mission h3{font-size:28px;font-weight:400;color:var(--white);letter-spacing:1px;margin-bottom:18px}
.mission p{font-size:13px;line-height:15.5px;width:290px;margin-bottom:18px;color:var(--white)}
.f-col h4{font-size:13.5px;font-weight:500;color:var(--white);letter-spacing:1px;margin-bottom:22px}
.links li{list-style:none;font-size:13px;line-height:30.5px;display:flex;align-items:center;gap:16px;color:var(--white)}
.links li::before{content:"";width:12px;height:12px;border-radius:50%;background:var(--white)}
.contact .item{position:relative;padding-left:34px;padding-bottom:22px;margin-bottom:22px;border-bottom:1px dashed #3a3a3a;width:260px}
.contact .item:last-child{border:none}
.contact .ic{position:absolute;left:0;top:0;width:22px;height:22px;border-radius:50%;background:var(--gold)}
.contact .label{color:var(--gold);font-size:12.5px;font-weight:500;margin-bottom:4px}
.contact .val{font-size:12.5px;line-height:16px;color:var(--white)}
.copyright{left:0;top:2752px;width:1200px;text-align:center;font-size:12.5px;color:var(--footer-text)}
</style>
</head>
<body>

<header class="hero abs">
  <div class="hero-portrait abs" role="img" aria-label="Photo of a smiling woman in a scarf and cardigan"></div>
</header>
<div class="menu-icon abs" aria-label="Menu"><span></span><span></span><span></span></div>
<div class="ribbon-top abs"><div class="mark"></div></div>
<h1 class="hero-title abs"><div class="line1">PINECREST HARBOR</div><div class="line2">FOUNDATION</div></h1>
<svg class="ribbon-bottom abs" viewBox="0 0 149 195"><polygon points="0,0 149,0 149,195 74.5,140 0,195" fill="var(--gold)"/></svg>
<div class="hero-dots abs"><i></i><i class="on"></i><i></i><i></i></div>

<section>
  <div class="causes-bg abs" role="img" aria-label="Soft faded photo of hands holding each other"></div>
  <p class="intro abs">We are a registered 501(c)3 non-profit that focuses on financially supporting the treatment of cancer patients that have been told they have no hope and there is nothing the conventional medical system can do for them.</p>
  <div class="divider abs"></div>
  <h2 class="section-title causes-title abs">FEATURED <em>CAUSES</em></h2>

  <article class="cause-card abs" style="left:98px">
    <div class="photo" role="img" aria-label="Photo of a smiling child patient"></div>
    <div class="progress"><div class="track"><div class="fill"></div></div><span class="pct">30%</span></div>
    <div class="stats"><span>Raised: $300,000</span><span>Goal: $800,000</span></div>
    <p class="desc">Neque porro quisquam<br>est qui dolorem ipsum<br>quia dolor sit</p>
    <span class="btn">Donate Now</span>
  </article>
  <article class="cause-card abs" style="left:443px">
    <div class="photo" role="img" aria-label="Photo of a doctor visiting an elderly patient in bed"></div>
    <div class="progress"><div class="track"><div class="fill"></div></div><span class="pct">30%</span></div>
    <div class="stats"><span>Raised: $300,000</span><span>Goal: $800,000</span></div>
    <p class="desc">Neque porro quisquam<br>est qui dolorem ipsum<br>quia dolor sit</p>
    <span class="btn">Donate Now</span>
  </article>
  <article class="cause-card abs" style="left:787px">
    <div class="photo" role="img" aria-label="Photo of a nurse helping an elderly woman"></div>
    <div class="progress"><div class="track"><div class="fill"></div></div><span class="pct">30%</span></div>
    <div class="stats"><span>Raised: $300,000</span><span>Goal: $800,000</span></div>
    <p class="desc">Neque porro quisquam<br>est qui dolorem ipsum<br>quia dolor sit</p>
    <span class="btn">Donate Now</span>
  </article>
</section>

<section class="team">
  <div class="team-photo abs" role="img" aria-label="Photo of volunteers packing a donation box outdoors"></div>
  <svg class="team-panel abs" viewBox="0 0 1200 465"><polygon points="658,0 1200,0 1200,465 547,465" fill="var(--gold)"/></svg>
  <h2 class="team-title abs">WE ARE<br>NONPROFIT TEAM</h2>
  <p class="team-text abs">Lorem ipsum dolor sit amet, consectetur adipisicing elit, sed do eiusmod tempor iont incididunt ut labore et dolore magna aliqua. Ut enim ad minim veniam, quis nostrudi exercitation ullamco laboris nisi ut aliquip ex ea commodo consequat.</p>
  <span class="btn team-btn abs">Donate Now</span>
</section>

<section>
  <h2 class="section-title testi-title abs">TESTIMONIALS</h2>
  <article class="testi-card abs" style="left:148px">
    <div class="avatar" role="img" aria-label="Portrait photo of the reviewer"></div>
    <p class="quote">Lorem Ipsum is simply dummy text of the printing and typesetting industry. Lorem Ipsum has been the industry standard dummy text ever since the 1500s, when an unknown printer took a galley of type and scrambled</p>
    <span class="name">NADIA BROOKS</span>
  </article>
  <article class="testi-card abs" style="left:614px">
    <div class="avatar" role="img" aria-label="Portrait photo of the reviewer"></div>
    <p class="quote">Lorem Ipsum is simply dummy text of the printing and typesetting industry. Lorem Ipsum has been the industry standard dummy text ever since the 1500s, when an unknown printer took a galley of type and scrambled it to make a type specimen book.</p>
    <span class="name">SELIN</span>
  </article>
  <div class="testi-dots abs"><i></i><i></i><i></i></div>
</section>

<footer>
  <div class="footer abs"></div>
  <div class="callbar abs">
    <svg class="phone-icon" viewBox="0 0 24 24"><path fill="#1b1b1b" d="M6.6 10.8a15.1 15.1 0 0 0 6.6 6.6l2.2-2.2c.3-.3.7-.4 1-.2 1.1.4 2.3.6 3.6.6.6 0 1 .4 1 1V20c0 .6-.4 1-1 1A17 17 0 0 1 3 4c0-.6.4-1 1-1h3.5c.6 0 1 .4 1 1 0 1.3.2 2.5.6 3.6.1.3 0 .7-.2 1z"/></svg>
    <div class="ask">DO YOU HAVE<br>A QUESTION?</div>
    <div class="number">+0123 456 789</div>
    <div class="email"><svg width="14" height="11" viewBox="0 0 14 11"><rect width="14" height="11" rx="1" fill="#9a9a9a"/><path d="M0 1l7 5 7-5" stroke="#fff" fill="none"/></svg>Enter Email Id</div>
    <div class="subscribe">Subscribe</div>
  </div>

  <div class="f-col mission abs" style="left:104px">
    <h3>OUR MISSION</h3>
    <p>Lorem ipsum dolor sit amet, consectetur adipisicing elit, sed do eiusmod tempor incididunt ut labore et dolore magna aliqua. Ut enim ad minim veniam.</p>
    <p>Quis nostrud exercitation ullamco laboris nisi ut aliquip ex ea commodo consequat. Duis aute irure dolor.</p>
  </div>
  <div class="f-col abs" style="left:562px">
    <h4>QUICK LINKS</h4>
    <ul class="links"><li>Home</li><li>About</li><li>Causes</li><li>Event</li><li>News</li><li>Contact</li></ul>
  </div>
  <div class="f-col contact abs" style="left:874px">
    <h4>CONTACT US</h4>
    <div class="item"><span class="ic"></span><div class="label">Head Office</div><div class="val">123, Main Street, Your City<br>USA 789456</div></div>
    <div class="item"><span class="ic"></span><div class="label">Phone Number</div><div class="val">+123 456 7890<br>+123 456 7890</div></div>
    <div class="item"><span class="ic"></span><div class="label">Email</div><div class="val">info@sitename.com<br>www.sitename.com</div></div>
  </div>
  <p class="copyright abs">Copyright © 2017, www.sitename.com, All Rights Reserved.</p>
</footer>

</body>
</html>
```